KMO Business card, letterhead, and stationery, email tag, fax cover
Clear and Professional material
Simple
Gérald Montaubry
Directeur des ventes
57, rue des Vergers Tilloux
Paris , 75016
France
gerald@kmosys.fr
www.kmosys.fr
Logo + tag line
LOGO
SMALL LOGO

```html
<!DOCTYPE html>
<html lang="fr">
<head>
<meta charset="utf-8">
<title>KMO – Cartes de visite</title>
<link rel="stylesheet" href="https://fonts.googleapis.com/css2?family=Open+Sans:wght@400;600;700&display=swap">
<style>
  :root {
    --backdrop: #2b2b2d;
    --card: #ffffff;
    --card-edge: #e4e5e7;
    --teal: #3bb4d3;
    --ink: #3a3a3c;
    --ink-soft: #6b6c70;
    --band-grey: #6f7074;
  }
  * { margin: 0; padding: 0; box-sizing: border-box; }
  html, body {
    width: 1200px; height: 945px; overflow: hidden;
    background: var(--backdrop);
    font-family: "Open Sans", Arial, sans-serif;
    color: var(--ink);
  }
  .canvas { position: relative; width: 1200px; height: 945px; }
  .card {
    position: absolute;
    background: linear-gradient(180deg, #ffffff 0%, #f6f7f8 100%);
    border: 1px solid var(--card-edge);
    border-radius: 22px;
    overflow: hidden;
  }
  .card-front { left: 140px; top: 140px; width: 620px; height: 395px; }
  .card-back  { left: 470px; top: 535px; width: 630px; height: 350px; }

  .brand { position: absolute; display: flex; flex-direction: column; }
  .brand-name {
    display: flex; align-items: center; gap: 10px;
    font-weight: 600; color: var(--ink-soft); line-height: 1.1;
  }
  .brand-dot { border-radius: 50%; background: var(--teal); flex: none; }
  .brand-tagline { color: var(--teal); font-weight: 400; }

  .card-front .brand { left: 40px; top: 95px; }
  .card-front .brand-name { font-size: 26px; }
  .card-front .brand-dot { width: 14px; height: 14px; }
  .card-front .brand-tagline { font-size: 15px; margin-top: 10px; margin-left: 24px; }

  .holder { position: absolute; right: 40px; top: 48px; text-align: right; }
  .holder-name { color: var(--teal); font-weight: 700; font-size: 23px; }
  .holder-role { font-size: 15px; margin-top: 4px; }

  .band { position: absolute; left: 0; top: 232px; width: 620px; height: 24px; }

  .contacts {
    position: absolute; left: 30px; top: 285px; right: 30px;
    display: flex; gap: 34px; font-size: 12.5px; line-height: 1.55;
  }
  .contacts .address { width: 195px; }
  .contacts .phones, .contacts .online {
    border-left: 2px solid var(--teal); padding-left: 8px;
  }
  .contacts b { font-weight: 700; }

  .card-back .brand { left: 50%; top: 50%; transform: translate(-50%, -50%); align-items: flex-start; }
  .card-back .brand-name { font-size: 30px; }
  .card-back .brand-dot { width: 16px; height: 16px; }
  .card-back .brand-tagline { font-size: 17px; margin-top: 10px; margin-left: 26px; }
</style>
</head>
<body>
<main class="canvas">

  <section class="card card-front" aria-label="Recto de la carte de visite">
    <div class="brand">
      <div class="brand-name"><span class="brand-dot"></span>Orvane Lumis Systems</div>
      <div class="brand-tagline">solutions avancées de la peau</div>
    </div>

    <div class="holder">
      <div class="holder-name">Gérald Montaubry</div>
      <div class="holder-role">Directeur des ventes</div>
    </div>

    <svg class="band" viewBox="0 0 620 24" preserveAspectRatio="none" aria-hidden="true">
      <polygon points="0,0 235,0 222,24 0,24" fill="var(--band-grey)"/>
      <polygon points="240,6 620,6 620,20 233,20" fill="var(--teal)"/>
    </svg>

    <div class="contacts">
      <div class="address">
        57, rue des Vergers Tilloux<br>
        Paris , 75016<br>
        France
      </div>
      <div class="phones">
        <b>P</b> | 01.45.17.60.32<br>
        <b>C</b> | 06.38.71.24.59<br>
        <b>F</b> | 01.45.17.60.33
      </div>
      <div class="online">
        <b>E</b> | gerald@kmosys.fr<br>
        <b>W</b> | www.kmosys.fr
      </div>
    </div>
  </section>

  <section class="card card-back" aria-label="Verso de la carte de visite">
    <div class="brand">
      <div class="brand-name"><span class="brand-dot"></span>Orvane Lumis Systems</div>
      <div class="brand-tagline">solutions avancées de la peau</div>
    </div>
  </section>

</main>
</body>
</html>
```